Business card design for Brivo Engineering Tandem

We need a new business card design along with all the necessary to place an order. The company is Brivo Engineering Tandem and we recently updated our logo.

```html
<!DOCTYPE html>
<html lang="en">
<head>
<meta charset="utf-8">
<title>Brivo Engineering Tandem — Business Card</title>
<link href="https://fonts.googleapis.com/css2?family=Poppins:wght@400;500;600&display=swap" rel="stylesheet">
<style>
  :root {
    --stage: #1b1b1c;
    --card: #2b2b2d;
    --card-edge: #333336;
    --accent: #e9c21f;
    --grey: #a3a3a6;
    --light: #d9d9dc;
    --panel-dark: #252527;
    --panel-light: #8d8d90;
  }
  * { margin: 0; padding: 0; box-sizing: border-box; }
  html, body { width: 1200px; height: 689px; overflow: hidden; }
  body {
    background: var(--stage);
    font-family: "Poppins", sans-serif;
    position: relative;
  }
  .card {
    position: absolute;
    top: 190px;
    width: 530px;
    height: 303px;
    background: var(--card);
    border: 1px solid var(--card-edge);
    border-radius: 18px;
    overflow: hidden;
  }
  .card--front { left: 45px; }
  .card--back { left: 625px; }

  .wordmark {
    display: flex;
    align-items: center;
    gap: 10px;
    font-weight: 600;
    color: var(--grey);
    letter-spacing: 0.06em;
    text-transform: uppercase;
    line-height: 1;
  }
  .wordmark__mark {
    width: 14px; height: 14px;
    background: var(--accent);
    flex: none;
  }
  .card--front .wordmark {
    position: absolute;
    left: 0; right: 0; top: 50%;
    transform: translateY(-50%);
    justify-content: center;
    font-size: 24px;
  }
  .card--back .wordmark {
    position: absolute;
    left: 36px; top: 40px;
    font-size: 17px;
  }

  .decor-panel {
    position: absolute;
    right: 0; top: 0;
    width: 190px; height: 100%;
    background: linear-gradient(160deg, var(--panel-dark) 0%, #3a3a3c 45%, var(--panel-light) 100%);
    clip-path: polygon(30% 0, 100% 0, 100% 100%, 0 100%);
  }
  .card--front .decor-panel {
    width: 170px;
    background: linear-gradient(160deg, #2e2e30 0%, #333335 60%, #3a3a3c 100%);
  }

  .person {
    position: absolute;
    left: 36px; top: 108px;
    padding-left: 14px;
  }
  .person__bar {
    position: absolute;
    left: 0; top: 0; bottom: 6px;
    width: 7px;
    background: var(--accent);
  }
  .person__name {
    font-size: 19px;
    font-weight: 600;
    color: var(--accent);
    letter-spacing: 0.02em;
    text-transform: uppercase;
    line-height: 1.15;
  }
  .person__role {
    font-size: 11px;
    font-weight: 500;
    color: var(--light);
    letter-spacing: 0.08em;
    text-transform: uppercase;
  }

  .contacts {
    position: absolute;
    left: 50px; top: 172px;
    list-style: none;
    font-size: 12.5px;
    color: var(--light);
    line-height: 1.55;
  }
  .contacts li { display: flex; align-items: center; gap: 8px; }
  .contacts svg { width: 12px; height: 12px; flex: none; }

  .address {
    position: absolute;
    left: 70px; top: 240px;
    font-size: 12.5px;
    color: var(--light);
    line-height: 1.45;
    font-style: normal;
  }
</style>
</head>
<body>

<section class="card card--front">
  <div class="decor-panel" role="img" aria-label="Large faint brand symbol decoration"></div>
  <div class="wordmark"><span class="wordmark__mark"></span>Brivo Engineering Tandem</div>
</section>

<section class="card card--back">
  <div class="decor-panel" role="img" aria-label="Large metallic brand symbol decoration"></div>
  <div class="wordmark"><span class="wordmark__mark"></span>Brivo Engineering Tandem</div>

  <div class="person">
    <span class="person__bar"></span>
    <div class="person__name">Marcus Delaney</div>
    <div class="person__role">Managing Director</div>
  </div>

  <ul class="contacts">
    <li>
      <svg viewBox="0 0 24 24" aria-hidden="true"><path fill="#e9c21f" d="M6.6 10.8a15.5 15.5 0 0 0 6.6 6.6l2.2-2.2c.3-.3.7-.4 1-.2 1.1.4 2.3.6 3.6.6.6 0 1 .4 1 1V20c0 .6-.4 1-1 1A17 17 0 0 1 3 4c0-.6.4-1 1-1h3.5c.6 0 1 .4 1 1 0 1.3.2 2.5.6 3.6.1.3 0 .7-.2 1z"/></svg>
      044-555 010 234
    </li>
    <li>
      <svg viewBox="0 0 24 24" aria-hidden="true"><path fill="#e9c21f" d="M3 5h18v14H3z"/><path fill="none" stroke="#2b2b2d" stroke-width="2" d="M3 5l9 8 9-8"/></svg>
      hello@brivotandem.com
    </li>
    <li>
      <svg viewBox="0 0 24 24" aria-hidden="true"><g fill="none" stroke="#e9c21f" stroke-width="2"><circle cx="12" cy="12" r="9"/><path d="M3 12h18M12 3c3 3 3 15 0 18M12 3c-3 3-3 15 0 18"/></g></svg>
      www.brivotandem.com
    </li>
  </ul>

  <address class="address">48, Harbor Lane<br>Northvale, 204518</address>
</section>

</body>
</html>
```